Dashboard Elements

Hello – looking for someone to create dashboard elements.
I’ve already basically designed all these elements – but I need someone to take what I’ve designed and make it look like an actual dashboard UI, like an app - assuming using some kind of dashboard UI kit (but however you would like to get it done is fine). It can look just like mine or try something different, as long as it matches the color scheme webpage that I’m going to out it on – see the page here. I’m ok with making it dark, maybe that would look better – again as long as it matches the webpage (https://www.plandeck.io/file/7QxKtr2BwLpZnVe4Hs8Mc1/Webpage-with-placeholders?node-id=0%3A1). Please note, you do not need to put anything on the webpage or do anything with this Figma file, this is just a reference so you can color/stylize it accordingly.

The attached Powerpoint file has everything you need - make sure to zoom all the way out to see everything on the slides.

Here are the Dashboard elements needed (this will all make sense when you look at the PPT):
Dashboard 1
Dashboard 1 – expanded view A
Dashboard 1 – expanded view B
View Source button by itself
Source Document Viewer 1 and 2 (these are exactly the same just with a different image inside)*
Dashboard 2 (only slightly different than Dashboard 1, just extended with extra headings
Table of Contents
Searchbar and Source Doc by itself
*the documents in the source document viewers should still look like documents - they don’t need to look like part of the UI, because this is a document viewer – you can restyle/recolor if necessary or just leave these as is.
- Colors must match color scheme of webpage, attached and on Figma link (images there currently are only placeholders) – ok to go dark as long as it matches
- Must look sleek, clean, realistic
- Don’t add any pictures of people or change the text.
- In case it’s not clear, this is what I mean by the concept of Dashboard UI - https://www.notavia.net/shard/s7/sh/8fad21bc-14e9-4a7c-b2d0-5c3e9f71a604/92c4e1b7a05d3f68e1c2b947d0a3f815
- Must be sent in an editable file, I may need to be edit text and other elements
- If you are going to send a sample, please make sure it’s part of the dashboard itself, not just the table of contents etc

Ideally hoping to find someone I can continue working with as I'll have a lot more graphic design work needed coming up.

Thank you!

```html
<!DOCTYPE html>
<html lang="en">
<head>
<meta charset="utf-8">
<title>Dashboard 1 – HCC Summary</title>
<link href="https://fonts.googleapis.com/css2?family=Open+Sans:wght@300;400;600;700&display=swap" rel="stylesheet">
<style>
  :root{
    --page:#d5e2e4;
    --teal:#2bb8c3;
    --teal-bright:#3fd6d8;
    --blue:#3f8fd0;
    --violet:#7c6bd8;
    --violet-soft:#a291e6;
    --navy:#0d4f9c;
    --ink-dark:#252849;
    --header-dark:#27365a;
    --pill:#27c7cc;
    --button:#8a6fe2;
    --white:#ffffff;
    --label:#1c1c1c;
  }
  *{box-sizing:border-box;margin:0;padding:0}
  html,body{width:1200px;height:1200px;overflow:hidden}
  body{background:var(--page);font-family:"Open Sans",Arial,sans-serif;position:relative;color:var(--white)}
  .slide-label{position:absolute;transform:translate(-50%,-50%) rotate(-90deg);color:var(--label);font-weight:300;font-size:26px;line-height:1.25;text-align:center;white-space:nowrap}
  .label-top{left:100px;top:325px}
  .label-bottom{left:110px;top:916px}

  .stage{position:absolute;left:204px;width:950px;height:575px;overflow:hidden;
    background:
      radial-gradient(ellipse 70% 80% at 95% 45%, rgba(63,143,208,.95) 0%, rgba(63,143,208,.6) 55%, rgba(63,143,208,0) 75%),
      linear-gradient(170deg, #2cbac4 0%, #3aa4cd 35%, #6a86d6 65%, #7d6bd8 100%);}
  .stage-top{top:17px}
  .stage-bottom{top:607px}
  .deco{position:absolute;background:rgba(255,255,255,.85);border-radius:3px}
  .deco.faint{background:rgba(255,255,255,.18)}

  .dash{position:absolute;left:50px;top:47px;width:858px;height:483px;border-radius:60px;overflow:hidden;
    box-shadow:0 0 0 3px rgba(140,120,230,.6),0 8px 20px rgba(40,40,120,.3)}
  .sidebar{position:absolute;inset:0;background:linear-gradient(180deg,#0c55a0 0%,#1378a6 45%,#15a69d 100%)}
  .nav-main{position:absolute;left:18px;top:72px;display:flex;align-items:center;gap:8px;font-size:14px;font-weight:600}
  .nav-main .caret{margin-left:26px;width:12px;height:12px;border-radius:50%;background:var(--white)}
  .nav-sub{position:absolute;left:0;top:96px;width:190px;height:21px;background:#1cbcc0;border-left:3px solid #45e0e0;font-size:9px;line-height:21px;padding-left:43px}
  .sidebar .deco{border-radius:4px}

  .main{position:absolute;left:178px;top:0;right:0;bottom:0;border-radius:46px 0 0 46px;
    background:
      radial-gradient(ellipse 60% 70% at 100% 80%, rgba(110,140,220,.55) 0%, rgba(110,140,220,0) 70%),
      linear-gradient(180deg,#6ec0d9 0%,#7fa9de 40%,#9a8fe2 100%)}
  .abs{position:absolute;white-space:nowrap}
  .brand-bar{left:4px;top:26px;width:444px;height:38px;border-radius:19px;background:linear-gradient(90deg,#27a7b7,#31b1bd);
    display:flex;align-items:center;padding-left:18px;box-shadow:0 3px 6px rgba(20,60,110,.3)}
  .brand-mark{width:16px;height:16px;background:var(--white);border-radius:2px;margin-right:10px}
  .brand-name{font-size:19px;font-weight:400;letter-spacing:.5px}
  .product{margin-left:auto;margin-right:22px;font-size:18px;font-weight:600}
  .patient{left:478px;top:32px;font-size:15px}
  .patient .caret{display:inline-block;width:12px;height:12px;border-radius:50%;background:var(--violet);margin-left:10px;vertical-align:-1px}
  .patient-meta{left:478px;top:57px;font-size:9px}
  .bell{left:626px;top:31px}
  .summary-title{left:30px;top:96px;font-size:16px;display:flex;align-items:center;gap:12px}
  .search{left:173px;top:94px;width:182px;height:26px;border:1.5px solid var(--violet-soft);border-radius:13px;font-size:9px;display:flex;align-items:center;padding-left:8px;gap:6px}
  .stat{top:99px;font-size:11px;font-weight:600}
  .count-ring{left:548px;top:94px;width:24px;height:24px;border-radius:50%;border:1.5px solid var(--violet-soft);font-size:14px;text-align:center;line-height:21px}
  .col-head{top:158px;font-size:11.5px;display:flex;align-items:center;gap:8px}
  .col-head i{width:10px;height:10px;border-radius:50%;background:var(--violet);display:inline-block}
  .col-rule{top:185px;width:88px;height:4px;border-radius:2px;background:var(--violet-soft)}
  .code{font-size:16px;font-weight:600}
  .cond{font-size:9px}
  .pill{width:84px;height:16px;border-radius:8px;background:var(--pill);box-shadow:0 0 6px rgba(80,230,230,.8);border:1.5px solid #aef3f0;font-size:9px;font-weight:600;text-align:center;line-height:13px}
  .raf{font-size:16px;font-weight:600}

  .expanded{position:absolute;left:142px;top:47px;width:684px;height:482px;border-radius:50px;overflow:hidden;
    box-shadow:0 0 0 3px rgba(55,210,210,.7);background:linear-gradient(180deg,#7ca9dc,#9d94e2)}
  .exp-head{position:absolute;left:0;top:0;width:100%;height:126px;background:var(--header-dark)}
  .band{position:absolute;left:0;width:100%}
  .why{position:absolute;left:0;top:84px;width:100%;text-align:center;font-size:10px}
  .why b{font-size:12px;font-weight:700}
  .src-label{font-size:12px}
  .src-type{font-size:12px;font-weight:600}
  .btn{display:flex;align-items:center;justify-content:center;gap:10px;border-radius:16px;font-weight:600}
  .btn-violet{width:154px;height:32px;background:var(--button);font-size:16px}
  .btn-teal{width:131px;height:30px;background:var(--pill);font-size:14px;border:1.5px solid #aef3f0;box-shadow:0 0 8px rgba(80,230,230,.8)}
  .popout{position:absolute;width:552px;height:98px;border-radius:16px;background:var(--ink-dark);
    box-shadow:0 0 0 6px rgba(60,215,215,.55),0 0 14px rgba(60,230,230,.8)}
  .pop-key{font-size:12px;color:var(--teal-bright);font-weight:600}
  .pop-title{font-size:12px;color:var(--button);font-weight:600}
  .pop-body{font-size:10px;line-height:12px}
</style>
</head>
<body>

<div class="slide-label label-top">Dashboard 1<br>with light vibrant colour scheme<br>plus frozen effect</div>
<div class="slide-label label-bottom">Dashboard 1 Expanded<br>View A</div>

<section class="stage stage-top">
  <span class="deco" style="left:900px;top:10px;width:24px;height:24px"></span>
  <span class="deco" style="left:10px;top:540px;width:30px;height:30px"></span>

  <div class="dash">
    <aside class="sidebar">
      <div class="nav-main">
        <svg width="20" height="14" viewBox="0 0 20 14"><path d="M2 12a8 8 0 0 1 16 0" fill="none" stroke="#fff" stroke-width="1.6"/><path d="M10 12l4-6" stroke="#fff" stroke-width="1.6"/></svg>
        Dashboard<span class="caret"></span>
      </div>
      <div class="nav-sub">HCC Summary</div>
      <span class="deco faint" style="left:36px;top:310px;width:70px;height:70px"></span>
      <span class="deco faint" style="left:124px;top:306px;width:30px;height:30px"></span>
      <span class="deco faint" style="left:68px;top:262px;width:24px;height:24px"></span>
    </aside>

    <main class="main">
      <div class="abs brand-bar">
        <span class="brand-mark"></span>
        <span class="brand-name">CLINIVUE</span>
        <span class="product">Chartwell Record Atlas</span>
      </div>
      <div class="abs patient">Patient, Alma<span class="caret"></span></div>
      <div class="abs patient-meta">Female | 01/11/1951 | Age: 70</div>
      <svg class="abs bell" width="24" height="22" viewBox="0 0 24 22"><path d="M4 17h14l-2-3V9a5 5 0 0 0-10 0v5z" fill="#8c6fe0"/><circle cx="11" cy="19" r="2" fill="#8c6fe0"/><circle cx="18" cy="5" r="5" fill="#8c6fe0"/><text x="18" y="7.5" font-size="7" fill="#fff" text-anchor="middle" font-family="Open Sans,sans-serif">3</text></svg>

      <div class="abs summary-title">
        <svg width="12" height="8" viewBox="0 0 12 8"><path d="M1 1l5 5 5-5" fill="none" stroke="#8c6fe0" stroke-width="2"/></svg>
        HCC Summary
      </div>
      <div class="abs search">
        <svg width="16" height="16" viewBox="0 0 16 16"><circle cx="6.5" cy="6.5" r="5" fill="none" stroke="#fff" stroke-width="1.6"/><path d="M10 10l5 5" stroke="#fff" stroke-width="1.8"/></svg>
        Search...
      </div>
      <div class="abs stat" style="left:386px">RAF: 2.362</div>
      <div class="abs stat" style="left:453px">Condition Count</div>
      <div class="abs count-ring">8</div>
      <div class="abs stat" style="left:584px">ID: 7326472</div>

      <div class="abs col-head" style="left:48px">ICD-10 Code <i></i></div>
      <div class="abs col-head" style="left:226px">Condition <i></i></div>
      <div class="abs col-head" style="left:423px">Catagory <i></i></div>
      <div class="abs col-head" style="left:562px">RAF <i></i></div>
      <span class="abs col-rule" style="left:46px"></span>
      <span class="abs col-rule" style="left:215px"></span>
      <span class="abs col-rule" style="left:412px"></span>

      <div class="abs code" style="left:48px;top:208px">J44.9</div>
      <div class="abs cond" style="left:176px;top:213px">Chronic obstructive pulmonary disease</div>
      <div class="abs pill" style="left:414px;top:210px">111</div>
      <div class="abs raf" style="left:557px;top:208px">0.335</div>

      <div class="abs code" style="left:48px;top:254px">F33.1</div>
      <div class="abs cond" style="left:176px;top:259px">Chronic kidney disease, moderate (stage 3)</div>
      <div class="abs pill" style="left:414px;top:256px">138</div>
      <div class="abs raf" style="left:557px;top:254px">0.069</div>

      <div class="abs code" style="left:48px;top:300px">F33.0</div>
      <div class="abs cond" style="left:176px;top:305px">Major depressive disorder, recurrent, mild</div>
      <div class="abs pill" style="left:414px;top:302px">59</div>
      <div class="abs raf" style="left:557px;top:300px">0.309</div>

      <div class="abs code" style="left:48px;top:345px">I42.9</div>
      <div class="abs cond" style="left:176px;top:350px">cardiomyopathy</div>
      <div class="abs pill" style="left:414px;top:347px">85</div>
      <div class="abs raf" style="left:557px;top:345px">0.447</div>

      <div class="abs code" style="left:48px;top:391px">E11.36</div>
      <div class="abs cond" style="left:176px;top:396px">Type 2 diabetes mellitus with diabetic cataract</div>
      <div class="abs pill" style="left:414px;top:393px">18</div>
      <div class="abs raf" style="left:557px;top:391px">0.302</div>

      <svg class="abs" style="left:610px;top:215px" width="14" height="200" viewBox="0 0 14 200">
        <g fill="none" stroke="#8c6fe0" stroke-width="2">
          <path d="M2 2l5 5 5-5"/><path d="M2 48l5 5 5-5"/><path d="M2 94l5 5 5-5"/><path d="M2 139l5 5 5-5"/><path d="M2 185l5 5 5-5"/>
        </g>
      </svg>
    </main>
  </div>
</section>

<section class="stage stage-bottom">
  <span class="deco faint" style="left:24px;top:34px;width:56px;height:56px"></span>
  <span class="deco" style="left:908px;top:16px;width:48px;height:48px"></span>
  <span class="deco" style="left:10px;top:542px;width:30px;height:30px"></span>
  <span class="deco faint" style="left:870px;top:520px;width:46px;height:46px;background:rgba(40,200,200,.6)"></span>

  <div class="expanded">
    <div class="exp-head">
      <div class="abs" style="left:54px;top:43px;font-size:16px;font-weight:600">E11.36</div>
      <div class="abs" style="left:182px;top:47px;font-size:9.5px">Type 2 diabetes mellitus with diabetic cataract</div>
      <div class="abs pill" style="left:420px;top:45px">18</div>
      <div class="abs" style="left:562px;top:43px;font-size:16px;font-weight:600">0.302</div>
      <svg class="abs" style="left:615px;top:50px" width="14" height="9" viewBox="0 0 14 9"><path d="M2 7l5-5 5 5" fill="none" stroke="#8c6fe0" stroke-width="2"/></svg>
      <p class="why"><b>Why:</b> This Patient was treated for cataracts that may be associated with type 2 diabates melitus</p>
    </div>

    <div class="band" style="top:126px;height:68px;background:rgba(255,255,255,.06)"></div>
    <div class="band" style="top:194px;height:88px;background:rgba(255,255,255,.12)"></div>
    <div class="band" style="top:282px;height:80px;background:rgba(255,255,255,.04)"></div>
    <div class="band" style="top:362px;height:84px;background:rgba(255,255,255,.12)"></div>

    <div class="abs src-label" style="left:59px;top:151px">Extacpsular cataract With IOL</div>
    <div class="abs src-type" style="left:288px;top:151px">C-CDA: Procedures</div>
    <div class="abs btn btn-violet" style="left:470px;top:142px">
      <svg width="18" height="16" viewBox="0 0 18 16"><path d="M1 15h16M3 13V9M7 13V7M11 13V5M15 13V3" stroke="#fff" stroke-width="2"/></svg>View Source
    </div>

    <div class="abs src-label" style="left:59px;top:314px">Diabetes Type 2</div>
    <div class="abs src-type" style="left:288px;top:314px">C-CDA: Problem list</div>
    <div class="abs btn btn-violet" style="left:470px;top:305px">
      <svg width="18" height="16" viewBox="0 0 18 16"><path d="M1 15h16M3 13V9M7 13V7M11 13V5M15 13V3" stroke="#fff" stroke-width="2"/></svg>View Source
    </div>
  </div>

  <div class="popout" style="left:32px;top:237px">
    <div class="abs pop-key" style="left:47px;top:40px">Cataract</div>
    <div class="abs pop-title" style="left:166px;top:24px">Ophthalmology Chart Note</div>
    <div class="abs pop-body" style="left:166px;top:43px">Patient presents for cataract<br>evaluation in the right eye.</div>
    <div class="abs btn btn-teal" style="left:378px;top:34px">
      <svg width="16" height="14" viewBox="0 0 18 16"><path d="M1 15h16M3 13V9M7 13V7M11 13V5M15 13V3" stroke="#fff" stroke-width="2"/></svg>View Source
    </div>
  </div>

  <div class="popout" style="left:364px;top:402px">
    <div class="abs pop-key" style="left:46px;top:40px">HbA1c</div>
    <div class="abs pop-title" style="left:166px;top:18px">Lab Results</div>
    <div class="abs pop-body" style="left:166px;top:37px">Hemoglobin A1C<br>6.9%<br>01/15/21</div>
    <div class="abs btn btn-teal" style="left:378px;top:34px">
      <svg width="16" height="14" viewBox="0 0 18 16"><path d="M1 15h16M3 13V9M7 13V7M11 13V5M15 13V3" stroke="#fff" stroke-width="2"/></svg>View Source
    </div>
  </div>
</section>

</body>
</html>
```